Business Card Design Project

We need a business card for a new technology services company. We develop software and implement software packages for our business customers and although we will begin with just one or two service offerings, our service offerings will expand over time. Our name comes from the an author, KL Barrow, and his "idea" was that opportunity should be based on ability and achievement, not on social status.

We would like to see a design that is standard in its size and shape, but stands apart in its dramatic color contrasts. The card should not use too many colors - the colors used in the background should highlight the brilliant blues of the logo (see attachment) to dramatic effect. The background should not be white.

If necessary, you can change the color of the words "KL Barrow", but not the word "Idea".

Card size should be U.S. standard 2 inches by 3.5 inches and provide for 1/8 inch bleed area on each side.

We need a design for both sides of the business card, one side communicating the company logo and contact information, the other side being purely graphical, incorporating the logo but no other information.

Contact Information Required:
Kate Brook
KateBrook@klbarrowvista.com
614-387-2259

Target Market(s)

Business executives

Industry/Entity Type

Software

Requirements
Must have
• It must have the full company logo on one side, and at least the graphic element of the logo on the other. Either that or the full logo on both.
Nice to have
• It would be nice to have a design that could work without needing two different textures. For example, it would be nice if the entire card could be shiny, not just parts of the card.

It would also be nice if texture is something we could add later.
Should not have
• The card should not use the color green.

```html
<!DOCTYPE html>
<html lang="en">
<head>
<meta charset="utf-8">
<title>Meritfield Labs — Business Card</title>
<link rel="stylesheet" href="https://fonts.googleapis.com/css2?family=Roboto:wght@300;400&family=Cinzel:wght@500&display=swap">
<style>
  :root {
    --page: #e9e7e3;
    --card-dark: #2c2c2e;
    --card-darker: #1b1b1d;
    --brand-blue: #12a3e2;
    --brand-blue-faint: rgba(18, 163, 226, 0.28);
    --band-grey: #a5a6a8;
    --wordmark-grey: #b8b9bb;
    --text-light: #ffffff;
  }
  * { box-sizing: border-box; margin: 0; padding: 0; }
  html, body { width: 1200px; height: 750px; overflow: hidden; }
  body {
    background: var(--page);
    font-family: "Roboto", Arial, sans-serif;
    position: relative;
  }
  .card {
    position: absolute;
    top: 220px;
    width: 540px;
    height: 309px;
    border-radius: 18px;
    overflow: hidden;
    background: radial-gradient(ellipse at 40% 35%, var(--card-dark), var(--card-darker));
    box-shadow: 0 8px 22px rgba(0,0,0,0.25);
  }
  .card--front { left: 40px; }
  .card--back { left: 620px; }

  .card-sheen {
    position: absolute; inset: 0;
    background: linear-gradient(160deg, rgba(255,255,255,0.05), rgba(0,0,0,0.08));
  }

  /* Front */
  .brand-dot {
    position: absolute;
    left: 372px; top: 34px;
    width: 64px; height: 64px; border-radius: 50%;
    background: var(--brand-blue);
  }
  .wordmark {
    position: absolute;
    left: 60px; top: 118px;
    font-weight: 300;
    font-size: 44px;
    letter-spacing: -1px;
    color: var(--wordmark-grey);
    line-height: 1;
    white-space: nowrap;
  }
  .band-contact {
    position: absolute; left: 0; right: 0; top: 192px; height: 56px;
    background: var(--band-grey);
    display: flex; align-items: center; justify-content: flex-end;
    padding-right: 24px; gap: 12px;
    color: var(--text-light); font-size: 14px; font-weight: 400;
    white-space: nowrap;
  }
  .contact-item { display: flex; align-items: center; gap: 6px; }
  .contact-divider { width: 1px; height: 34px; background: rgba(255,255,255,0.7); }
  .band-name {
    position: absolute; left: 0; right: 0; top: 248px; height: 38px;
    background: var(--brand-blue);
    display: flex; align-items: center; justify-content: flex-end;
    padding-right: 90px;
  }
  .person-name {
    font-family: "Cinzel", Georgia, serif;
    font-size: 20px; letter-spacing: 1.5px;
    color: var(--text-light);
    white-space: nowrap;
  }

  /* Back */
  .back-circle {
    position: absolute; left: 190px; top: 20px;
    width: 270px; height: 270px; border-radius: 50%;
    background: var(--brand-blue-faint);
  }
  .back-wordmark {
    position: absolute; right: 36px; top: 126px;
    font-size: 60px; letter-spacing: -1.5px; font-weight: 300;
    color: var(--wordmark-grey); line-height: 1;
    white-space: nowrap;
  }
</style>
</head>
<body>
  <section class="card card--front" aria-label="Business card front">
    <div class="card-sheen"></div>
    <span class="brand-dot"></span>
    <span class="wordmark">Meritfield Labs</span>
    <div class="band-contact">
      <span class="contact-item">
        <svg width="13" height="13" viewBox="0 0 24 24" aria-hidden="true"><path fill="#fff" d="M6.6 10.8a15.1 15.1 0 0 0 6.6 6.6l2.2-2.2a1 1 0 0 1 1-.25 11.4 11.4 0 0 0 3.6.57 1 1 0 0 1 1 1V20a1 1 0 0 1-1 1A17 17 0 0 1 3 4a1 1 0 0 1 1-1h3.5a1 1 0 0 1 1 1c0 1.25.2 2.45.57 3.57a1 1 0 0 1-.25 1z"/></svg>
        614-387-2259
      </span>
      <span class="contact-divider"></span>
      <span class="contact-item">
        <svg width="13" height="11" viewBox="0 0 24 18" aria-hidden="true"><rect x="1" y="1" width="22" height="16" rx="2" fill="#fff"/><path d="M2 2l10 8 10-8" fill="none" stroke="#a5a6a8" stroke-width="2"/></svg>
        KateBrook@klbarrowvista.com
      </span>
    </div>
    <div class="band-name">
      <span class="person-name">KATE BROOK</span>
    </div>
  </section>

  <section class="card card--back" aria-label="Business card back">
    <div class="card-sheen"></div>
    <div class="back-circle"></div>
    <span class="back-wordmark">Meritfield Labs</span>
  </section>
</body>
</html>
```